Business Card for premium dental clinic

We are a premium dental clinic based in Brasov, Romania with more than 15 year on the market, providing quality dental treatment made by a team of more specialized dentists, working with modern equipment as a solution to beautiful and healthy teeth.

Our current logo for the clinic use 2 square with colors black and gold - dr Ternisu - studio, using family fonts Bodoni, Myriad Pro and Segoe Print.
Depending on the printing we used some gold CMYK background or gold foil picture background or a gold gradient.
We want a business card:
- eye catching business card
- distinguished business card
- premium design
- to keep the color scheme of black and gold
- to attract the customers to spent time reading the information
- modern concept

```html
<!DOCTYPE html>
<html lang="en">
<head>
<meta charset="utf-8">
<title>dr Ternisu – Business Card</title>
<link rel="stylesheet" href="https://fonts.googleapis.com/css2?family=Fira+Sans:wght@400;500&display=swap">
<style>
  :root {
    --backdrop: #9b9b9b;
    --paper: #f7f7f6;
    --gold: #f2b51f;
    --edge: #d4880f;
    --ink: #1e1e1e;
    --muted: #6f6f6f;
    --rule: #8a8a8a;
  }
  html, body {
    margin: 0;
    width: 1200px;
    height: 1059px;
    overflow: hidden;
    background: var(--backdrop);
    font-family: "Fira Sans", Arial, sans-serif;
  }
  .canvas {
    position: relative;
    width: 1200px;
    height: 1059px;
  }
  .card {
    position: absolute;
    width: 600px;
    height: 344px;
    background: var(--paper);
    border-bottom: 4px solid var(--edge);
    box-shadow: 0 18px 40px rgba(0,0,0,0.25);
    box-sizing: border-box;
  }
  .card--front { left: 60px; top: 120px; }
  .card--back { left: 540px; top: 580px; }

  .front-content {
    position: absolute;
    inset: 0;
    display: flex;
    flex-direction: column;
    align-items: center;
    justify-content: center;
    text-align: center;
  }
  .holder-name {
    color: var(--gold);
    font-size: 30px;
    font-weight: 500;
    letter-spacing: 1px;
    line-height: 1;
  }
  .holder-role {
    color: var(--ink);
    font-size: 16px;
    margin-top: 4px;
  }
  .divider {
    width: 260px;
    height: 1px;
    background: var(--rule);
    margin: 8px 0;
  }
  .address, .contact {
    color: var(--muted);
    font-size: 18px;
    line-height: 1.3;
    letter-spacing: 0.5px;
  }

  .brand-name {
    position: absolute;
    left: 50%;
    top: 50%;
    transform: translate(-50%, -50%);
    color: var(--ink);
    font-size: 34px;
    font-weight: 500;
    letter-spacing: 0.5px;
    white-space: nowrap;
  }
</style>
</head>
<body>
  <main class="canvas">
    <section class="card card--front" aria-label="Business card front">
      <div class="front-content">
        <div class="holder-name">Daniel Marsh</div>
        <div class="holder-role">President</div>
        <div class="divider"></div>
        <div class="address">4120 Linden Court<br>Brasov, Romania 500210</div>
        <div class="divider"></div>
        <div class="contact">268-410-7732 | hello@ternisuclinic.com<br>www.ternisuclinic.com</div>
      </div>
    </section>

    <section class="card card--back" aria-label="Business card back">
      <span class="brand-name">dr Ternisu</span>
    </section>
  </main>
</body>
</html>
```